Coastal Learner Bureau business cards

Australian company about to start offering its services. We recruit international students to come to study English, vocational education and postgraduate courses in Australia. We help them find the institution and select the right city they want to come to Australia. We are a young, online oriented and supportive agency. Our clients are between 18 and 35 years old, mainly University students, young professionals or people with work experience. We provide much more information that any other agency offer. We administrate a Facebook group with more than 11.000 members that daily ask questions about general information when coming to Australia, while they are here and even after they leave the country

Target Market(s)

International students from South America, Central America and Europe

Industry/Entity Type

Student

Contact Information for Business Card

Tomas Bilbrea
Managing Director
tomas@kelvarin.com.au
www.kelvoria.com.au
+61 491058264
Harbourton, Australia

Font styles to use
Serif
Sans Serif

Colors

Designer to choose colors to be used in the design.

Requirements
Must have
• Horizontal design
• Standard business card size and shape. If font uses green or yellow colours, they will have to match the ones from the logo
Nice to have
• UPDATE: Use the contents of the green image to design one of the card sides. Use our logo in the background of that side as watermark.
• Passport image, or immigration stamps. A picture of the Yarra River (from Melbourne) would be cool as well.
Should not have
• Non-standard business card size and shape
• Not black as the background colour of any sides as we are not a VIP agency or a hight class service. We are orientes to young people and they like colours, pictures, something attractive.
• Vertical design
• NO YELLOW or BLACK AS THE BACKGROUND COLOUR OF ANY SIDE OF THE BIZ CARD

```html
<!DOCTYPE html>
<html lang="en">
<head>
<meta charset="utf-8">
<title>Coastal Learner Bureau business cards</title>
<link href="https://fonts.googleapis.com/css2?family=Comic+Neue:wght@700&family=PT+Sans:wght@400;700&display=swap" rel="stylesheet">
<style>
  :root{
    --green:#12663f;
    --green-deep:#0d5634;
    --yellow:#f0c21b;
    --paper:#f5f5f3;
    --stage:#e6e4df;
    --ink-light:#ffffff;
  }
  *{box-sizing:border-box;margin:0;padding:0}
  html,body{width:1200px;height:886px;overflow:hidden}
  body{background:var(--stage);position:relative;font-family:"PT Sans",sans-serif}
  .card{
    position:absolute;width:540px;height:309px;border-radius:18px;overflow:hidden;
    box-shadow:0 10px 28px rgba(0,0,0,.18);
  }
  .card--front{left:45px;top:288px;background:linear-gradient(160deg,var(--green) 0%,var(--green-deep) 100%)}
  .card--back{left:615px;top:288px;background:var(--paper)}

  .brand-name{
    font-family:"Comic Neue",sans-serif;font-weight:700;letter-spacing:1px;
  }
  .front__brand{
    position:absolute;left:0;right:0;top:92px;text-align:center;
    color:var(--ink-light);font-size:72px;line-height:1;
  }
  .front__tagline{
    position:absolute;left:70px;right:70px;top:214px;
    display:flex;align-items:center;gap:10px;color:var(--ink-light);
    font-size:14px;font-weight:700;white-space:nowrap;
  }
  .front__tagline::before,.front__tagline::after{
    content:"";flex:1;height:1px;background:rgba(255,255,255,.6);
  }

  .back__waves{position:absolute;inset:0;width:540px;height:309px}
  .back__brand{
    position:absolute;right:50px;top:30px;display:flex;align-items:center;gap:10px;
    color:var(--green);font-size:50px;line-height:1;
  }
  .back__brand .dot{width:14px;height:14px;border-radius:50%;background:var(--yellow)}
  .contact{position:absolute;left:32px;top:198px;color:var(--ink-light)}
  .contact__name{
    font-family:"Comic Neue",sans-serif;font-weight:700;color:var(--yellow);
    font-size:20px;line-height:1.05;
  }
  .contact__role{font-size:13px;margin-bottom:4px}
  .contact__list{list-style:none}
  .contact__item{display:flex;align-items:center;gap:8px;font-size:11.5px;line-height:15px}
  .contact__item svg{width:11px;height:11px;flex:none}
</style>
</head>
<body>

<section class="card card--front" aria-label="Card front">
  <div class="front__brand brand-name">Kelvoria</div>
  <div class="front__tagline">Contigo en cada paso!</div>
</section>

<section class="card card--back" aria-label="Card back">
  <svg class="back__waves" viewBox="0 0 540 309" aria-hidden="true">
    <path fill="var(--green)" d="M0,192 C160,166 300,160 400,152 C470,146 515,132 540,116 L540,309 L0,309 Z"/>
    <path fill="var(--yellow)" d="M300,156 C400,148 480,130 540,98 L540,108 C490,134 420,150 300,156 Z"/>
    <path fill="var(--green)" d="M0,180 C130,152 260,142 350,136 C430,130 490,112 540,86 L540,92 C490,118 430,136 355,141 C260,147 130,160 0,186 Z"/>
  </svg>

  <div class="back__brand brand-name"><span>Kelvoria</span><span class="dot"></span></div>

  <div class="contact">
    <p class="contact__name">Tomas Bilbrea</p>
    <p class="contact__role">Managing Director</p>
    <ul class="contact__list">
      <li class="contact__item">
        <svg viewBox="0 0 12 12" aria-hidden="true"><path fill="var(--yellow)" d="M2.5 1l2 2-1 1.4c.6 1.4 1.7 2.5 3.1 3.1L8 6.5l2 2-1.4 2C5 10.2 1.8 7 1.5 2.5z"/></svg>
        <span>+61 491058264</span>
      </li>
      <li class="contact__item">
        <svg viewBox="0 0 12 12" aria-hidden="true"><rect x="1" y="2.5" width="10" height="7" fill="var(--yellow)"/><path d="M1 2.5l5 4 5-4" fill="none" stroke="var(--green)" stroke-width="1"/></svg>
        <span>tomas@kelvarin.com.au</span>
      </li>
      <li class="contact__item">
        <svg viewBox="0 0 12 12" aria-hidden="true"><circle cx="6" cy="6" r="5" fill="var(--yellow)"/><path d="M1 6h10M6 1c-2 2.5-2 7.5 0 10M6 1c2 2.5 2 7.5 0 10" fill="none" stroke="var(--green)" stroke-width=".8"/></svg>
        <span>www.kelvoria.com.au</span>
      </li>
      <li class="contact__item">
        <svg viewBox="0 0 12 12" aria-hidden="true"><path fill="var(--yellow)" d="M6 .5a4 4 0 0 1 4 4c0 3-4 7-4 7s-4-4-4-7a4 4 0 0 1 4-4z"/><circle cx="6" cy="4.5" r="1.5" fill="var(--green)"/></svg>
        <span>Harbourton, Australia</span>
      </li>
    </ul>
  </div>
</section>

</body>
</html>
```